Vindgerdi - Start-up company selling electricity

Hello let me tell you about Vindgerdi.

Vindgerdi is start-up company selling electricity in Iceland. The operations of the company consist of making power usage forecasts for our customers, purchasing the electricity wholesale from the energy producers, and selling the electricity to the consumer. We are focused on tech by using optimization and machine learning to minimize electricity prices to our customers. Our marketing strategy is to portray a tech company mindset and to show dedication to driving down the electricity price on the market.

We need your help to make our website pop. Possible concepts to work with are as follows:

- Iceland the land of ice and fire
- Green energy
- Innovation
- Tech and data science

Link to our website: https://prufa.vindgerdi-example.is/
We are open to ideas.
Thank you!

Target Market(s)

Electricity consumers both homes and companies.

Number of Pages Required

1 page

Font styles to use
Serif
Sans Serif

```html
<!DOCTYPE html>
<html lang="en">
<head>
<meta charset="utf-8">
<title>Vindgerdi</title>
<link rel="stylesheet" href="https://fonts.googleapis.com/css2?family=Bebas+Neue&family=Merriweather:wght@700;900&family=Montserrat:wght@700&family=Poppins:wght@300;400;500&display=swap">
<style>
:root{
  --red:#a32e24;
  --navy:#14305a;
  --ink:#000;
  --text:#555;
  --muted:#8a8a8a;
  --rule:#d9d9d9;
  --hero-bg:#fafafa;
  --city:#dedede;
  --card:#fafafa;
  --white:#fff;
}
*{margin:0;padding:0;box-sizing:border-box}
html,body{width:701px;height:1200px;overflow:hidden;background:var(--white)}
body{position:relative;font-family:'Poppins',sans-serif;color:var(--text)}
.abs{position:absolute}
.center{left:0;width:701px;text-align:center}

.hero{top:0;left:0;width:701px;height:394px;background:var(--hero-bg)}
.brand{top:20px;left:35px;display:flex;align-items:center;gap:7px}
.brand-dot{width:18px;height:18px;border-radius:50%;background:var(--navy)}
.brand-name{font-family:'Merriweather',serif;font-weight:900;font-size:21px;color:var(--red);letter-spacing:.3px}
.nav{top:31px;right:35px;display:flex;gap:18px;align-items:center;font-size:6.6px;font-weight:300;color:var(--muted);letter-spacing:.2px}
.hero-title{top:99px;font-family:'Bebas Neue',sans-serif;font-size:26px;font-weight:400;color:var(--navy);letter-spacing:.1px}
.hero-title span{color:var(--red)}
.hero-text{top:134px;left:192px;width:317px;font-size:7px;line-height:12px;text-align:center;color:var(--text)}
.btn{display:flex;align-items:center;justify-content:center;border-radius:2px;color:var(--white);font-size:8.2px;font-weight:400;text-decoration:none}
.btn-red{background:var(--red)}
.btn-navy{background:var(--navy)}
.btn-black{background:var(--ink)}
.city{top:210px;left:0;width:701px;height:179px;background:linear-gradient(180deg,var(--hero-bg) 0%,var(--city) 45%,var(--city) 100%);opacity:.85}
.ground{top:389px;left:0;width:701px;height:5px;background:var(--city)}

.section-title{font-family:'Montserrat',sans-serif;font-weight:700;font-size:19px;color:var(--ink);letter-spacing:.4px}
.divider{left:293px;width:115px;height:12px}
.divider::before,.divider::after{content:"";position:absolute;top:6px;width:49px;height:1px;background:var(--rule)}
.divider::before{left:0}.divider::after{right:0}
.divider i{position:absolute;left:53px;top:2px;width:8px;height:8px;border-radius:50%;background:var(--navy)}
.body-text{left:193px;width:315px;font-size:6.6px;line-height:11.9px;text-align:center;color:var(--muted)}

.card{background:var(--card);border:1px solid #eee;border-radius:2px}
.badge{display:flex;align-items:center;justify-content:center;font-family:'Bebas Neue',sans-serif;font-size:22px;color:var(--white);border:2px solid var(--white)}
.badge-red{background:var(--red);box-shadow:0 0 0 1px var(--red)}
.badge-navy{background:var(--navy);box-shadow:0 0 0 1px var(--navy)}
.unit{font-size:9px;color:#444;text-align:center}
.link-line{top:779px;height:1px;background:var(--rule)}
.node{width:9px;height:9px;border-radius:50%;background:#ccc;border:2px solid #f0f0f0;box-shadow:0 0 0 1px #ddd}

.footer{top:1016px;left:0;width:701px;height:184px;background:var(--ink);color:#ccc}
.foot-col{top:40px}
.foot-head{font-family:'Merriweather',serif;font-weight:700;font-size:8.6px;color:var(--white);margin-bottom:10px}
.foot-list{list-style:none;font-size:6.8px;line-height:13.2px;color:#bbb}
.foot-list li::before{content:"-\00a0\00a0"}
.contact{font-size:6.8px;line-height:13.2px;color:#bbb;border-collapse:collapse}
.contact td{padding:0}
.contact .k{width:34px;font-size:6.4px}
.contact .s{width:7px}
.foot-rule{top:149px;left:0;width:701px;height:1px;background:#222}
.copy{top:162px;font-size:6px;color:#bbb}
</style>
</head>
<body>

<header class="abs hero">
  <div class="abs brand"><span class="brand-dot"></span><span class="brand-name">VINDGERDI</span></div>
  <nav class="abs nav">
    <span>TERMS OF BUSINESS</span>
    <span>QUESTION &amp; ANSWER</span>
    <span>ABOUT VINDGERDI</span>
    <svg width="10" height="10" viewBox="0 0 10 10" aria-label="Search"><circle cx="4.2" cy="4.2" r="3.3" fill="none" stroke="#a32e24" stroke-width="1"/><line x1="6.6" y1="6.6" x2="9.3" y2="9.3" stroke="#a32e24" stroke-width="1"/></svg>
  </nav>
  <h1 class="abs center hero-title">SAME ELECTRICITY~<span>JUST CHEAPER!</span></h1>
  <p class="abs hero-text">Lorem ipsum dolor sit amet, consectetur adipiscing elit, sed do eiusmod tempor incididunt ut labore et dolore magna aliqua. Ut enim ad minim veniam, quis nostrud.</p>
  <a class="abs btn btn-red" style="top:167px;left:313px;width:75px;height:26px">CONTACT US</a>
  <div class="abs city" role="img" aria-label="Light grey city skyline with office towers, a factory chimney, trees and wind turbines"></div>
  <div class="abs ground"></div>
</header>

<h2 class="abs center section-title" style="top:436px">WELCOME TO BUSINESS</h2>
<div class="abs divider" style="top:464px"><i></i></div>
<p class="abs body-text" style="top:489px">Lorem ipsum dolor sit amet, consectetur adipiscing elit, sed do eiusmod tempor incididunt ut labore et dolore magna aliqua. Ut enim ad minim veniam, quis nostrud exercitation ullamco laboris nisi ut aliquip ex ea commodo consequat. Duis aute irure dolor in reprehenderit in voluptate velit esse cillum dolore eu fugiat nulla pariatur. Excepteur sint occaecat cupidatat non proident, sunt in culpa qui officia deserunt mollit anim id est laborum.</p>
<a class="abs btn btn-navy" style="top:565px;left:276px;width:70px;height:26px">COMPANY</a>
<a class="abs btn btn-red" style="top:565px;left:355px;width:70px;height:26px">HOME</a>

<h2 class="abs center section-title" style="top:633px">PRICE LIST</h2>
<div class="abs divider" style="top:661px"><i></i></div>
<p class="abs center" style="top:686px;font-size:9.5px;color:#555">Make a price comparison</p>

<div class="abs link-line" style="left:245px;width:70px"></div>
<div class="abs link-line" style="left:385px;width:70px"></div>
<div class="abs card" style="top:747px;left:79px;width:166px;height:65px"></div>
<div class="abs card" style="top:747px;left:456px;width:166px;height:65px"></div>
<div class="abs badge badge-red" style="top:723px;left:137px;width:51px;height:51px">6.95</div>
<div class="abs badge badge-navy" style="top:723px;left:514px;width:51px;height:51px">6.22</div>
<p class="abs unit" style="top:787px;left:79px;width:166px">ISK / kWh</p>
<p class="abs unit" style="top:787px;left:456px;width:166px">ISK / kWh electric acceleration</p>
<span class="abs node" style="top:775px;left:241px"></span>
<span class="abs node" style="top:775px;left:451px"></span>
<a class="abs btn btn-black" style="top:767px;left:315px;width:71px;height:26px">VERDVAKT</a>

<h2 class="abs center section-title" style="top:856px">THE FUTURE IS EXCITING</h2>
<div class="abs divider" style="top:884px"><i></i></div>
<p class="abs body-text" style="top:909px">Let's make the electricity system smarter together. Vindgerdi uses artificial intelligence, data science and automation to minimize costs and promote eccentricity.</p>
<a class="abs btn btn-red" style="top:946px;left:313px;width:75px;height:26px">CONTACT US</a>

<footer class="abs footer">
  <div class="abs foot-col" style="left:36px">
    <h3 class="foot-head">VINDGERDI EHF</h3>
    <ul class="foot-list"><li>ID number: 510101-2290</li><li>VAT number: 120456</li></ul>
  </div>
  <div class="abs foot-col" style="left:253px">
    <h3 class="foot-head">LINKS</h3>
    <ul class="foot-list"><li>Terms of business</li><li>Question &amp; Answer</li><li>About Vindgerdi</li></ul>
  </div>
  <div class="abs foot-col" style="left:469px">
    <h3 class="foot-head">GET IN TOUCH</h3>
    <table class="contact">
      <tr><td class="k">ADDRESS</td><td class="s">:</td><td>Dæmigata 12, 999 Vindabær</td></tr>
      <tr><td class="k">EMAIL</td><td class="s">:</td><td>hallo@vindgerdi-example.is</td></tr>
      <tr><td class="k">PHONE</td><td class="s">:</td><td>555-0199</td></tr>
    </table>
  </div>
  <div class="abs foot-rule"></div>
  <p class="abs center copy">Copyright © Vindgerdi 2020 - All rights reserved</p>
</footer>

</body>
</html>
```